Business cards for Zestcycle

We need a business card layout for our new bike and e-bike rental (we also sell used e-bikes and bike accessories). The logo already exists.

```html
<!DOCTYPE html>
<html lang="en">
<head>
<meta charset="utf-8">
<title>Zestcycle – Business Cards</title>
<link rel="stylesheet" href="https://fonts.googleapis.com/css2?family=Lato:wght@300;400;700;900&family=Mulish:wght@400;500&display=swap">
<style>
  :root {
    --backdrop: #232323;
    --mint-light: #63c8aa;
    --mint-dark: #4b9883;
    --ink-dark: #1e3a3b;
    --navy-light: #20363a;
    --navy-dark: #172a2e;
    --accent: #5ec3a6;
    --white: #ffffff;
    --muted: #e6eeee;
  }
  * { margin: 0; padding: 0; box-sizing: border-box; }
  html, body {
    width: 1200px; height: 960px; overflow: hidden;
    background: var(--backdrop);
  }
  .canvas { position: relative; width: 1200px; height: 960px; }

  .card {
    position: absolute;
    width: 600px; height: 342px;
    border-radius: 22px;
    overflow: hidden;
  }

  /* Front */
  .card-front {
    left: 302px; top: 124px;
    background: linear-gradient(100deg, var(--mint-light) 0%, var(--mint-light) 45%, var(--mint-dark) 100%);
    text-align: center;
    font-family: "Lato", sans-serif;
  }
  .brand-dot {
    position: absolute; left: 50%; top: 62px;
    width: 40px; height: 40px; margin-left: -20px;
    border: 3px solid var(--white); border-radius: 50%;
  }
  .brand-name {
    position: absolute; left: 0; right: 0; top: 124px;
    font-size: 66px; font-weight: 400; letter-spacing: 1px;
    color: var(--ink-dark); line-height: 1;
  }
  .tagline {
    position: absolute; left: 0; right: 0; top: 216px;
    font-size: 18px; font-weight: 700; color: var(--white);
  }
  .service-title {
    position: absolute; left: 0; right: 0; top: 268px;
    font-size: 25px; font-weight: 900; color: var(--ink-dark); line-height: 1;
    padding-right: 16px;
  }
  .service-note {
    position: absolute; left: 0; right: 0; top: 292px;
    font-family: "Mulish", sans-serif;
    font-size: 16px; color: var(--white); line-height: 1;
    padding-right: 16px;
  }

  /* Back */
  .card-back {
    left: 299px; top: 493px;
    background: linear-gradient(120deg, var(--navy-light) 0%, var(--navy-dark) 100%);
    font-family: "Mulish", sans-serif;
    color: var(--muted);
  }
  .person-name {
    position: absolute; left: 65px; top: 74px;
    font-family: "Lato", sans-serif; font-weight: 700;
    font-size: 24px; color: var(--accent); line-height: 1;
  }
  .person-role {
    position: absolute; left: 65px; top: 101px;
    font-family: "Lato", sans-serif; font-weight: 700;
    font-size: 15px; color: var(--white); line-height: 1;
  }
  .divider {
    position: absolute; left: 65px; width: 149px;
    border-top: 1.5px dotted rgba(255,255,255,0.75);
  }
  .divider-top { top: 131px; }
  .divider-bottom { top: 193px; }
  .address {
    position: absolute; left: 65px; top: 147px;
    font-size: 14px; line-height: 18px; font-style: normal;
  }
  .contact-list {
    position: absolute; left: 65px; top: 210px;
    list-style: none; font-size: 14px; line-height: 19px;
  }
  .contact-list li { display: flex; align-items: center; }
  .contact-list svg { width: 12px; height: 12px; margin-right: 9px; fill: var(--accent); }
  .back-brand {
    position: absolute; left: 410px; top: 225px; width: 140px;
    text-align: center;
    font-family: "Lato", sans-serif; font-weight: 700;
    font-size: 20px; letter-spacing: 1px; color: var(--white);
  }
</style>
</head>
<body>
<main class="canvas">
  <section class="card card-front" aria-label="Front of business card">
    <span class="brand-dot" aria-hidden="true"></span>
    <h1 class="brand-name">ZESTCYCLE</h1>
    <p class="tagline">ride easy, ride far</p>
    <h2 class="service-title">NEW BIKE &amp; E-BIKE RENTAL</h2>
    <p class="service-note">We also sell used e-bikes &amp; bike accessories</p>
  </section>

  <section class="card card-back" aria-label="Back of business card">
    <h3 class="person-name">MARA LINDQVIST</h3>
    <p class="person-role">CEO/FOUNDER</p>
    <div class="divider divider-top"></div>
    <address class="address">2140 Alder Grove Road<br>Fairbanks, Alaska 99701</address>
    <div class="divider divider-bottom"></div>
    <ul class="contact-list">
      <li>
        <svg viewBox="0 0 24 24" aria-hidden="true"><path d="M6.6 10.8a15.1 15.1 0 0 0 6.6 6.6l2.2-2.2c.3-.3.7-.4 1-.2 1.1.4 2.3.6 3.6.6.6 0 1 .4 1 1V20c0 .6-.4 1-1 1C10.6 21 3 13.4 3 4c0-.6.4-1 1-1h3.5c.6 0 1 .4 1 1 0 1.3.2 2.5.6 3.6.1.3 0 .7-.2 1z"/></svg>
        907 215 6480
      </li>
      <li>
        <svg viewBox="0 0 24 24" aria-hidden="true"><path d="M2 5h20v14H2z"/><path d="M2 6l10 7.5L22 6" fill="none" stroke="var(--navy-light)" stroke-width="2"/></svg>
        mara@zestcycle.com
      </li>
      <li>
        <svg viewBox="0 0 24 24" aria-hidden="true"><circle cx="12" cy="12" r="10"/></svg>
        www.zestcycle.com
      </li>
    </ul>
    <p class="back-brand">ZESTCYCLE</p>
  </section>
</main>
</body>
</html>
```